Redesign of business card for Cedar Ridge Mechanical

We are looking for a new design for our business cards for Cedar Ridge Mechanical. We are a plumbing & HVAC construction company, operating on the West Coast of Canada and USA. Logo attached.
Industry/Entity Type
Construction - Plumbing & HVAC
Contact Information for Business Card
Name, address, phone numbers, email, website address
Look and feel
Each slider illustrates characteristics of the customer's brand and the style your logo design should communicate.

```html
<!DOCTYPE html>
<html lang="en">
<head>
<meta charset="utf-8">
<title>Cedar Ridge Mechanical – Business Card</title>
<link rel="stylesheet" href="https://fonts.googleapis.com/css2?family=Poppins:wght@300;400;600&display=swap">
<style>
  :root {
    --backdrop: #3b4046;
    --card: #1f1f21;
    --ink: #eeeeee;
    --ink-soft: #cfcfcf;
    --ghost: #2a2a2d;
    --rule: #d8d8d8;
  }
  * { box-sizing: border-box; margin: 0; padding: 0; }
  html, body { width: 1200px; height: 780px; overflow: hidden; }
  body {
    background: var(--backdrop);
    font-family: "Poppins", sans-serif;
    color: var(--ink);
    position: relative;
  }
  .card {
    position: absolute;
    top: 236px;
    width: 540px;
    height: 308px;
    background: var(--card);
    border-radius: 22px;
    overflow: hidden;
  }
  .card--back { left: 40px; }
  .card--front { left: 620px; }

  /* Front */
  .front-brand {
    position: absolute;
    inset: 0;
    display: flex;
    align-items: center;
    justify-content: center;
    gap: 16px;
  }
  .brand-square {
    width: 22px; height: 22px;
    border: 3px solid var(--ink);
  }
  .brand-name {
    font-weight: 600;
    font-size: 26px;
    letter-spacing: 1px;
    text-transform: uppercase;
    color: var(--ink);
  }

  /* Back */
  .ghost-name {
    position: absolute;
    left: 26px; top: 60px;
    font-weight: 600;
    font-size: 44px;
    line-height: 1;
    color: var(--ghost);
    text-transform: uppercase;
    width: 220px;
  }
  .person {
    position: absolute;
    left: 36px; top: 64px;
  }
  .person-name { font-size: 28px; line-height: 1.1; }
  .person-name .first { font-weight: 600; }
  .person-name .last { font-weight: 300; }
  .person-title { font-size: 12px; font-weight: 300; color: var(--ink-soft); margin-top: 4px; }
  .divider {
    position: absolute;
    left: 150px; right: 0; top: 150px;
    height: 1.5px;
    background: var(--rule);
  }
  .back-brand {
    position: absolute;
    right: 32px; top: 40px;
    display: flex; align-items: center; gap: 10px;
  }
  .back-brand .brand-name { font-size: 17px; }
  .back-brand .brand-square { width: 16px; height: 16px; border-width: 2px; }
  .contact {
    position: absolute;
    right: 28px; bottom: 26px;
    list-style: none;
    text-align: right;
    font-size: 13.5px;
    font-weight: 300;
    line-height: 1.45;
  }
  .contact li { display: flex; justify-content: flex-end; align-items: center; gap: 10px; }
  .contact svg { width: 14px; height: 14px; flex: none; }
  .contact .no-icon { padding-right: 24px; }
</style>
</head>
<body>
  <section class="card card--back" aria-label="Card back with contact details">
    <div class="ghost-name" aria-hidden="true">Cedar Ridge</div>
    <div class="person">
      <p class="person-name"><span class="first">Marta</span> <span class="last">Lindqvist</span></p>
      <p class="person-title">Founder &amp; CEO</p>
    </div>
    <div class="divider"></div>
    <div class="back-brand">
      <span class="brand-square"></span>
      <span class="brand-name">Cedar Ridge Mechanical</span>
    </div>
    <ul class="contact">
      <li class="no-icon">4180 Harbor Ln. Suite 310</li>
      <li class="no-icon">Portland, OR 97205</li>
      <li>(503) 555-0147
        <svg viewBox="0 0 24 24" aria-hidden="true"><path fill="#eeeeee" d="M6.6 10.8a15.1 15.1 0 0 0 6.6 6.6l2.2-2.2a1 1 0 0 1 1-.25 11.4 11.4 0 0 0 3.6.57 1 1 0 0 1 1 1V20a1 1 0 0 1-1 1A17 17 0 0 1 3 4a1 1 0 0 1 1-1h3.5a1 1 0 0 1 1 1c0 1.25.2 2.45.57 3.57a1 1 0 0 1-.25 1z"/></svg>
      </li>
      <li>info@yourwebsite.com
        <svg viewBox="0 0 24 24" aria-hidden="true"><rect x="2" y="5" width="20" height="14" rx="1.5" fill="#eeeeee"/><path d="M3 6l9 7 9-7" stroke="#1f1f21" stroke-width="2" fill="none"/></svg>
      </li>
      <li>www.yourwebsite.com
        <svg viewBox="0 0 24 24" aria-hidden="true"><circle cx="12" cy="12" r="10" fill="#eeeeee"/><path d="M2 12h20M12 2c3 3 3 17 0 20M12 2c-3 3-3 17 0 20" stroke="#1f1f21" stroke-width="1.5" fill="none"/></svg>
      </li>
    </ul>
  </section>

  <section class="card card--front" aria-label="Card front">
    <div class="front-brand">
      <span class="brand-square"></span>
      <span class="brand-name">Cedar Ridge Mechanical</span>
    </div>
  </section>
</body>
</html>
```